Fenwick Grading LTD - website for irrigation & Landscape Lighting & Buried service wire

Looking for a website to help promote my business with Irrigation (installation, service, etc) and buried service wire/drainage solutions.

Commercial/Residential

Landscape lighting.

I’ll get photos in the trucks and trailers to upload as well maybe the machine as well.

Target Market(s)

Homeowners who want green grass and beautiful gardens. Beautiful landscape lighting

Industry/Entity Type

Irrigation systems and landscape lighting and buried service wire to homes and offering Drainage soltions.

Coding

Coded - Design and coding required

Number of Pages Required

4 page

Colors
F0912C
F2A743
F7CA91
FBE8D2
FDF5EE

Requirements
Must have
• was hoping to link up my email on fenwickgrading@mailbox-example.net with the website if possible.
Nice to have
• Page for Irrigation, page for landscape lighting, page buried service wire & drainage soltions.

```html
<!DOCTYPE html>
<html lang="en">
<head>
<meta charset="utf-8">
<title>Fenwick Grading LTD</title>
<link rel="stylesheet" href="https://fonts.googleapis.com/css2?family=Montserrat:wght@400;500;600;700&family=Roboto+Condensed:wght@700&display=swap">
<style>
  :root {
    --orange: #F0912C;
    --orange-light: #F2A743;
    --peach: #F7CA91;
    --cream: #FBE8D2;
    --blush: #FDF5EE;
    --ink: #111111;
    --text: #222222;
    --muted: #555555;
    --white: #ffffff;
    --black: #000000;
  }
  * { margin: 0; padding: 0; box-sizing: border-box; }
  html, body { width: 1200px; height: 3200px; overflow: hidden; background: var(--white); }
  body { position: relative; font-family: "Montserrat", sans-serif; color: var(--text); }
  .abs { position: absolute; }

  /* Header */
  .brand { position: absolute; font-family: "Montserrat", sans-serif; font-weight: 700; letter-spacing: 1px; line-height: 1.05; }
  .brand--header { left: 140px; top: 30px; font-size: 21px; color: var(--white); }
  .nav { position: absolute; top: 34px; font-size: 13px; color: var(--white); }
  .nav a { color: inherit; text-decoration: none; position: absolute; white-space: nowrap; }
  .nav a.is-active { color: var(--orange); text-decoration: underline; text-underline-offset: 4px; }
  .btn { position: absolute; background: var(--orange); color: var(--white); font-size: 12px; font-weight: 600; letter-spacing: 1px; border-radius: 20px; display: flex; align-items: center; justify-content: center; text-transform: uppercase; white-space: nowrap; }

  /* Hero */
  .hero-art { position: absolute; left: 0; top: 0; }
  .hero-title { left: 140px; top: 186px; font-family: "Roboto Condensed", sans-serif; font-weight: 700; font-size: 39px; line-height: 48.5px; color: var(--white); width: 540px; }
  .hero-copy { left: 140px; top: 343px; width: 480px; font-size: 12.6px; line-height: 22.5px; color: var(--white); font-weight: 500; }

  /* Sections */
  .section-title { left: 0; width: 1200px; text-align: center; top: 700px; font-family: "Roboto Condensed", sans-serif; font-weight: 700; font-size: 37px; color: var(--ink); }
  .accent { color: var(--orange); }
  .service-title { font-size: 25px; font-weight: 500; color: var(--ink); white-space: nowrap; }
  .service-sub { border-left: 2px solid var(--orange); padding-left: 11px; font-size: 12.6px; line-height: 22.6px; color: var(--ink); font-weight: 500; }
  .service-body { font-size: 12.6px; line-height: 22.6px; color: var(--muted); }

  /* Testimonials */
  .testi-title { left: 0; width: 1200px; text-align: center; top: 2240px; font-size: 25px; font-weight: 500; color: var(--ink); }
  .testi-sub { left: 0; width: 1200px; text-align: center; top: 2291px; font-size: 12.6px; font-weight: 500; color: var(--ink); }
  .quote { left: 140px; top: 2421px; width: 480px; font-size: 12.6px; line-height: 22.6px; color: var(--text); }
  .quote-name { left: 140px; top: 2552px; font-size: 15.5px; font-weight: 500; color: var(--orange); }

  /* Footer */
  .brand--footer { left: 0; width: 1200px; top: 2905px; text-align: center; font-size: 30px; color: var(--orange); }
  .foot-nav { top: 3015px; font-size: 12.8px; color: var(--white); }
  .foot-nav span { position: absolute; white-space: nowrap; }
  .contact-text { font-size: 12.8px; line-height: 21px; color: var(--white); white-space: nowrap; }
  .rule { left: 140px; top: 3136px; width: 920px; height: 1px; background: #333; }
  .copyright { left: 140px; top: 3160px; font-size: 12.6px; color: var(--white); }
</style>
</head>
<body>

<!-- Hero -->
<svg class="hero-art" width="1200" height="630" viewBox="0 0 1200 630">
  <defs>
    <linearGradient id="heroGrad" x1="0" y1="0" x2="1" y2="1">
      <stop offset="0" stop-color="#3d4a2c"/>
      <stop offset="0.45" stop-color="#4d6a2a"/>
      <stop offset="0.75" stop-color="#5a7a34"/>
      <stop offset="1" stop-color="#3a3b30"/>
    </linearGradient>
    <linearGradient id="heroShade" x1="0" y1="0" x2="1" y2="0">
      <stop offset="0" stop-color="#000" stop-opacity="0.45"/>
      <stop offset="0.6" stop-color="#000" stop-opacity="0.15"/>
      <stop offset="1" stop-color="#000" stop-opacity="0.3"/>
    </linearGradient>
  </defs>
  <polygon points="0,547 600,620 1200,540 1200,532 600,608 0,540" fill="var(--orange)"/>
  <g role="img" aria-label="Photo of a lit garden path with lawn, shrubs and bollard lights at dusk">
    <polygon points="0,0 1200,0 1200,532 600,608 0,540" fill="url(#heroGrad)"/>
    <polygon points="0,0 1200,0 1200,532 600,608 0,540" fill="url(#heroShade)"/>
  </g>
</svg>

<div class="brand brand--header">FENWICK<br>GRADING LTD</div>
<nav class="nav">
  <a class="is-active" style="left:385px">Home</a>
  <a style="left:469px">Irrigation</a>
  <a style="left:574px">Landscape Lighting</a>
  <a style="left:748px">Buried Service Wire</a>
</nav>
<div class="btn" style="left:939px;top:25px;width:120px;height:34px;">Contact Us</div>

<h1 class="abs hero-title">Transform Your Outdoor Space With Our Expert Irrigation And Lighting Solutions</h1>
<p class="abs hero-copy">Get The Perfect Blend Of Form And Function With Our State-Of-The-Art Irrigation Systems And Landscape Lighting. Trust Our Experienced Team With Buried Service Wire And Drainage For Your Home</p>
<div class="btn" style="left:140px;top:431px;width:234px;height:38px;">Free No Obligation Quotes</div>

<!-- Intro -->
<h2 class="abs section-title">One Stop Solution For <span class="accent">All Outdoor Home Improvements</span></h2>

<!-- Irrigation -->
<svg class="abs" style="left:175px;top:816px" width="436" height="395" viewBox="0 0 436 395">
  <defs>
    <linearGradient id="g1" x1="0" y1="0" x2="0" y2="1">
      <stop offset="0" stop-color="#8fa3b8"/>
      <stop offset="0.5" stop-color="#b8c2c8"/>
      <stop offset="1" stop-color="#4f5a4a"/>
    </linearGradient>
  </defs>
  <polyline points="0,15 218,392 436,15" fill="none" stroke="var(--orange)" stroke-width="1.5"/>
  <polygon role="img" aria-label="Photo of an irrigation sprinkler head spraying water" points="0,0 436,0 218,378" fill="url(#g1)"/>
</svg>
<h3 class="abs service-title" style="left:646px;top:860px">Irrigation <span class="accent">Systems</span></h3>
<p class="abs service-sub" style="left:646px;top:914px;width:380px">Efficient and Effective Watering Solutions for Your Lawn and Garden</p>
<p class="abs service-body" style="left:646px;top:973px;width:420px">Our irrigation systems are designed to provide your lawn and garden with the right amount of water, without wasting a single drop. With our expert installation and service, you can rest assured that your plants will receive the nourishment they need to thrive.</p>
<div class="btn" style="left:646px;top:1112px;width:123px;height:34px;">Learn More</div>

<!-- Landscape Lighting -->
<svg class="abs" style="left:622px;top:1293px" width="436" height="395" viewBox="0 0 436 395">
  <defs>
    <linearGradient id="g2" x1="0" y1="0" x2="0" y2="1">
      <stop offset="0" stop-color="#3a3820"/>
      <stop offset="0.4" stop-color="#7a7a22"/>
      <stop offset="1" stop-color="#3b4a18"/>
    </linearGradient>
  </defs>
  <polyline points="0,15 218,392 436,15" fill="none" stroke="var(--orange)" stroke-width="1.5"/>
  <polygon role="img" aria-label="Photo of a glowing bollard light beside a lawn at night" points="0,0 436,0 218,378" fill="url(#g2)"/>
</svg>
<h3 class="abs service-title" style="left:140px;top:1337px">Landscape <span class="accent">Lighting</span></h3>
<p class="abs service-sub" style="left:140px;top:1391px;width:410px">Enhance Your Outdoor Space with Beautiful and Functional Lighting Solutions</p>
<p class="abs service-body" style="left:140px;top:1450px;width:410px">Our landscape lighting solutions are designed to enhance the beauty and functionality of your outdoor space. From subtle pathway lighting to dramatic spotlights, we'll work with you to create a lighting plan that meets your needs and complements your landscape.</p>
<div class="btn" style="left:140px;top:1589px;width:123px;height:34px;">Learn More</div>

<!-- Service wire & drainage -->
<svg class="abs" style="left:175px;top:1770px" width="436" height="395" viewBox="0 0 436 395">
  <defs>
    <linearGradient id="g3" x1="0" y1="0" x2="1" y2="1">
      <stop offset="0" stop-color="#6d8a3a"/>
      <stop offset="0.5" stop-color="#8a9a6a"/>
      <stop offset="1" stop-color="#4a5a28"/>
    </linearGradient>
  </defs>
  <polyline points="0,15 218,392 436,15" fill="none" stroke="var(--orange)" stroke-width="1.5"/>
  <polygon role="img" aria-label="Photo of a spade digging into grassy soil" points="0,0 436,0 218,378" fill="url(#g3)"/>
</svg>
<h3 class="abs service-title" style="left:638px;top:1836px">Wire &amp; <span class="accent">Drainage</span></h3>
<p class="abs service-sub" style="left:638px;top:1890px;width:420px">Buried Service Wire and Drainage Solutions Done Right</p>
<p class="abs service-body" style="left:638px;top:1927px;width:430px">We trench and bury service wire to your home cleanly and safely, and we fix soggy yards with drainage built to last. From first dig to final grade, your lawn is left neat and ready.</p>
<div class="btn" style="left:638px;top:2042px;width:123px;height:34px;">Learn More</div>

<!-- Testimonials -->
<h2 class="abs testi-title">What Our <span class="accent">Customers</span> Say</h2>
<p class="abs testi-sub">Hear from Our Satisfied Clients</p>
<p class="abs quote">They maintain around 52 acres for us including several thousand sq ft or beds. Always answer thr phone and very prompt if we ever have an issue. Great guys all the way around! It is a long established fact that a reader will be distracted by the readable content of a page when looking at its layout.</p>
<p class="abs quote-name">Marcus Tellier</p>

<svg class="abs" style="left:140px;top:2624px" width="130" height="20" viewBox="0 0 130 20">
  <path d="M36 10H2M9 3L2 10l7 7" fill="none" stroke="var(--ink)" stroke-width="1.6"/>
  <path d="M92 10h36M121 3l7 7-7 7" fill="none" stroke="var(--ink)" stroke-width="1.6"/>
</svg>

<svg class="abs" style="left:585px;top:2295px" width="480" height="400" viewBox="0 0 480 400">
  <defs>
    <linearGradient id="p1" x1="0" y1="0" x2="0" y2="1">
      <stop offset="0" stop-color="#c9d3dc"/>
      <stop offset="1" stop-color="#2a2f38"/>
    </linearGradient>
    <linearGradient id="p2" x1="0" y1="0" x2="0" y2="1">
      <stop offset="0" stop-color="#e8d8d0"/>
      <stop offset="1" stop-color="#b01a2a"/>
    </linearGradient>
    <linearGradient id="p3" x1="0" y1="0" x2="0" y2="1">
      <stop offset="0" stop-color="#7fb0b8"/>
      <stop offset="1" stop-color="#2f3a3a"/>
    </linearGradient>
    <linearGradient id="p4" x1="0" y1="0" x2="0" y2="1">
      <stop offset="0" stop-color="#d0d4d8"/>
      <stop offset="1" stop-color="#3a3532"/>
    </linearGradient>
  </defs>
  <rect x="132" y="60" width="234" height="336" rx="117" fill="none" stroke="var(--orange)" stroke-width="1.5"/>
  <rect role="img" aria-label="Portrait photo of the featured customer" x="127" y="55" width="232" height="339" rx="116" fill="url(#p1)"/>
  <circle role="img" aria-label="Portrait photo of a customer" cx="416" cy="60" r="56" fill="url(#p2)"/>
  <circle role="img" aria-label="Portrait photo of a customer" cx="47" cy="315" r="40" fill="url(#p3)"/>
  <circle role="img" aria-label="Portrait photo of a customer" cx="416" cy="320" r="35" fill="url(#p4)"/>
</svg>

<!-- Footer -->
<svg class="abs" style="left:0;top:2770px" width="1200" height="430" viewBox="0 0 1200 430">
  <polygon points="0,77 600,6 1200,77 1200,430 0,430" fill="var(--orange)"/>
  <polygon points="0,85 600,16 1200,85 1200,430 0,430" fill="var(--black)"/>
</svg>
<div class="brand brand--footer">FENWICK<br>GRADING LTD</div>

<div class="abs foot-nav" style="left:0">
  <span style="left:279px;color:var(--orange)">Home</span>
  <span style="left:369px">Irrigation</span>
  <span style="left:478px">Landscape Lighting</span>
  <span style="left:656px">Buried Service Wire</span>
  <span style="left:853px;font-weight:600">Contact Us</span>
</div>

<svg class="abs" style="left:205px;top:3073px" width="800" height="40" viewBox="0 0 800 40">
  <g fill="none" stroke="var(--orange)" stroke-width="1.5">
    <circle cx="20" cy="20" r="17"/>
    <circle cx="341" cy="20" r="17"/>
    <circle cx="577" cy="20" r="17"/>
  </g>
  <g fill="var(--white)">
    <path d="M20 11a6 6 0 0 0-6 6c0 4.5 6 11 6 11s6-6.5 6-11a6 6 0 0 0-6-6zm0 8.3a2.3 2.3 0 1 1 0-4.6 2.3 2.3 0 0 1 0 4.6z"/>
    <path d="M335 13c1-1 2-1 2.6 0l1.6 2.6c.5.8.2 1.6-.5 2.1l-.9.6c.8 1.8 2.2 3.2 4 4l.6-.9c.5-.7 1.3-1 2.1-.5l2.6 1.6c1 .6 1 1.6 0 2.6-1.5 1.5-3.5 1.8-6 .4-3-1.7-5.3-4-7-7-1.4-2.5-1.1-4.5.4-6z"/>
    <path d="M569 14h16v12h-16zM569.5 14.5l7.5 6 7.5-6" stroke="var(--black)" stroke-width="1.2"/>
  </g>
</svg>
<p class="abs contact-text" style="left:251px;top:3072px">123, Building Name, Street<br>City, State XY 123456</p>
<p class="abs contact-text" style="left:572px;top:3072px">Phone<br>123-456-7890</p>
<p class="abs contact-text" style="left:810px;top:3072px">E-Mail<br>info@fenwickgrading.example</p>

<div class="abs rule"></div>
<p class="abs copyright">© 2024 Fenwick Grading Ltd . All Rights Reserved.</p>

<svg class="abs" style="left:902px;top:3150px" width="160" height="36" viewBox="0 0 160 36" role="img" aria-label="Social media links">
  <g fill="none" stroke="var(--white)" stroke-width="1.2">
    <circle cx="18" cy="18" r="15.5"/>
    <circle cx="59" cy="18" r="15.5"/>
    <circle cx="99" cy="18" r="15.5"/>
    <circle cx="140" cy="18" r="15.5"/>
  </g>
</svg>

</body>
</html>
```